Kestrelway Financial Plans

I am looking for a complete resdesign of my small financial presentation. This is a Word Doc/PDF that I print off when meeting with people in private. I often present my "two pager" that I have been using for years and years. It tells them the basics of what I do, how I help people and foundational financial principles.

I have recently gone out on my own in business and have completely rebranded. This presentation is my most used tool, so it is the first of many things I would like to redo. I am hoping it will somehow coordinate with the colors of my business, not necessarily the EXACT same 3 colors everywhere, but have the design colors compliment.

I've uploaded all my logo designs, as well as the current "two-pager". I am not against it going to 3 pages if needed. As it will still land on 2 pages with duplex printing.

It has always been VERY simple. I am wanting it built into a more professional and design specific format, to show off my branding, without being over cluttered.

I am completely open to ANY graphics changes. Obviously some are very novice, the house on the last page has always been overly simplified.

```html
<!DOCTYPE html>
<html lang="en">
<head>
<meta charset="utf-8">
<title>Kestrelway Financial Plans</title>
<link rel="stylesheet" href="https://fonts.googleapis.com/css2?family=Montserrat:wght@600&family=Roboto:ital,wght@0,400;0,500;0,700;0,900;1,400&display=swap">
<style>
  :root {
    --green: #0ea63e;
    --navy: #0c1b31;
    --slate: #8a8d92;
    --backdrop: #5b5b5b;
    --ink: #1d1d1f;
    --body: #4a4a4a;
    --rule: #e4e4e4;
    --oxblood: #781818;
    --partner: #cfe2f5;
  }
  * { box-sizing: border-box; margin: 0; padding: 0; }
  html, body { width: 1200px; height: 2987px; overflow: hidden; }
  body { background: var(--backdrop); font-family: 'Roboto', sans-serif; position: relative; }
  .page { position: absolute; left: 59px; width: 1082px; overflow: hidden; }
  .page-one { top: 59px; height: 1402px; background: #fff; }
  .page-two { top: 1526px; height: 1400px; background: linear-gradient(160deg, #ffffff 0%, #f4f4f4 55%, #ebebeb 100%); }
  .abs { position: absolute; }

  /* header */
  .masthead { left: 20px; top: 21px; width: 1041px; height: 159px; border: 1.5px solid var(--green); border-radius: 14px; text-align: center; }
  .brand-name { font-family: 'Montserrat', sans-serif; font-weight: 600; color: var(--navy); font-size: 58px; letter-spacing: 1px; margin-top: 24px; line-height: 1; }
  .brand-tag { font-family: 'Montserrat', sans-serif; font-weight: 600; color: var(--navy); font-size: 22px; letter-spacing: 5px; margin-top: 14px; }

  /* challenge section */
  .section-title { left: -185px; top: 437px; width: 460px; height: 40px; transform: rotate(-90deg); font-weight: 900; font-size: 33px; color: var(--navy); text-align: center; line-height: 40px; letter-spacing: 0.3px; }
  .section-line { left: 44px; top: 706px; width: 3px; height: 220px; background: var(--green); }
  .topic-pill { left: 92px; width: 240px; height: 78px; border-radius: 39px; color: #fff; font-weight: 500; font-size: 22px; display: flex; align-items: center; padding-left: 36px; gap: 20px; }
  .topic-pill svg { width: 24px; height: 24px; }
  .pill-savings { top: 231px; background: var(--green); }
  .pill-debt { top: 392px; background: var(--slate); }
  .pill-insurance { top: 553px; background: var(--navy); }
  .facts { left: 370px; width: 690px; font-size: 14.4px; line-height: 33px; color: var(--body); }
  .facts .line { position: relative; padding-left: 22px; white-space: nowrap; }
  .facts .line.marked::before { content: ""; position: absolute; left: 0; top: 11px; width: 11px; height: 11px; border: 1.5px solid var(--green); border-radius: 50%; background: radial-gradient(circle, var(--green) 2px, transparent 2.5px); }
  .facts-savings { top: 221px; }
  .facts-debt { top: 381px; }
  .facts-insurance { top: 542px; }

  /* services oval */
  .oval { left: 0; top: 0; }
  .oval-heading { left: 0; width: 1082px; text-align: center; color: #fff; font-weight: 700; font-size: 34px; line-height: 41px; top: 744px; }
  .service { width: 200px; text-align: center; }
  .service .badge { width: 106px; height: 106px; border-radius: 50%; background: #fff; margin: 0 auto; display: flex; align-items: center; justify-content: center; }
  .service .badge svg { width: 64px; height: 64px; }
  .service .label { color: #fff; font-weight: 700; font-size: 14.5px; margin-top: 20px; white-space: nowrap; }
  .edu-pill { left: 368px; top: 1083px; width: 345px; height: 57px; border-radius: 29px; background: var(--green); color: #fff; font-weight: 700; font-size: 17px; display: flex; align-items: center; justify-content: center; }
  .how-heading { left: 0; width: 1082px; text-align: center; top: 1168px; color: #fff; font-weight: 700; font-size: 35px; }
  .tiny-label { color: #fff; font-size: 7px; font-style: italic; font-weight: 700; text-align: center; width: 40px; }
  .goal-pill { left: 433px; width: 112px; height: 22px; border-radius: 11px; background: #fff; display: flex; align-items: center; gap: 6px; padding-left: 3px; }
  .goal-pill .dot { width: 16px; height: 16px; border-radius: 50%; background: var(--green); flex: none; }
  .goal-pill span { font-size: 6.5px; font-style: italic; color: #888; }
  .partner { height: 26px; border-radius: 7px; background: var(--partner); }

  /* rule of 72 */
  .rule-heading { left: 78px; top: 40px; font-weight: 700; font-size: 34px; color: var(--ink); letter-spacing: 0.3px; }
  .growth-card { width: 286px; background: #fff; border-radius: 34px 34px 24px 24px; box-shadow: 0 8px 20px rgba(0,0,0,0.09); overflow: hidden; }
  .growth-head { height: 66px; background: var(--green); border-radius: 34px; color: #fff; font-size: 21px; display: flex; align-items: center; justify-content: space-between; padding: 0 38px 0 42px; }
  .growth-head b { font-weight: 700; }
  .growth-row { height: 72px; display: flex; border-top: 1px solid var(--rule); color: var(--body); font-size: 20px; }
  .growth-row:first-of-type { border-top: none; }
  .growth-row .age { width: 143px; border-right: 1px solid var(--rule); display: flex; align-items: center; padding-left: 46px; }
  .growth-row .amount { flex: 1; display: flex; align-items: center; justify-content: flex-end; padding-right: 30px; }
  .growth-note { font-size: 15.5px; color: var(--ink); letter-spacing: 0.3px; white-space: nowrap; }

  /* account cards */
  .account { left: 403px; width: 607px; border-radius: 22px; color: #fff; }
  .account.navy { background: var(--navy); }
  .account.green { background: var(--green); }
  .account .icon { position: absolute; left: 28px; top: 42px; width: 64px; height: 64px; border-radius: 50%; display: flex; align-items: center; justify-content: center; }
  .account.navy .icon { background: var(--green); }
  .account.green .icon { background: var(--navy); }
  .account .icon svg { width: 32px; height: 32px; }
  .account h3 { position: absolute; left: 120px; top: 30px; font-size: 24px; font-weight: 700; }
  .account ul { position: absolute; left: 120px; top: 70px; list-style: none; font-size: 15px; line-height: 26px; }
  .account li { position: relative; padding-left: 26px; }
  .account li::before { content: ""; position: absolute; left: 0; top: 7px; width: 12px; height: 12px; border: 1.5px solid #fff; border-radius: 50%; background: radial-gradient(circle, #fff 2.2px, transparent 2.7px); }
  .account .tag { position: absolute; right: 29px; top: 37px; height: 30px; min-width: 90px; padding: 0 20px; border-radius: 15px; font-weight: 700; font-size: 14.5px; display: flex; align-items: center; justify-content: center; }
  .account.navy .tag { background: var(--green); }
  .account.green .tag { background: var(--navy); }
  .side-note { left: 78px; font-weight: 700; font-size: 14.5px; color: var(--ink); line-height: 27px; letter-spacing: 0.3px; }
  .side-rule { left: 78px; top: 1260px; width: 325px; height: 1px; background: #777; }
</style>
</head>
<body>

<section class="page page-one">
  <header class="masthead abs">
    <div class="brand-name">KESTRELWAY</div>
    <div class="brand-tag">FINANCIAL PLANS</div>
  </header>

  <h2 class="section-title abs">THE FINANCIAL CHALLENGE</h2>
  <div class="section-line abs"></div>

  <div class="topic-pill pill-savings abs">
    <svg viewBox="0 0 24 24"><path d="M11 2a10 10 0 1 0 10 11H11z" fill="#fff"/><path d="M13 0v11h11A11 11 0 0 0 13 0z" fill="#fff"/></svg>
    SAVINGS
  </div>
  <div class="topic-pill pill-debt abs">
    <svg viewBox="0 0 24 24"><path d="M2 3h9l10 10-8 8L3 11z" fill="#fff"/><circle cx="7" cy="7.5" r="1.8" fill="#8a8d92"/></svg>
    DEBT
  </div>
  <div class="topic-pill pill-insurance abs">
    <svg viewBox="0 0 24 24" fill="none" stroke="#fff" stroke-width="2.6"><path d="M4 11V7h14"/><path d="M15 4l3 3-3 3"/><path d="M20 13v4H6"/><path d="M9 20l-3-3 3-3"/></svg>
    INSURANCE
  </div>

  <div class="facts facts-savings abs">
    <div class="line marked">49% of canadian employees are living paycheque to paycheque. 25% of Canadians are unable to cover</div>
    <div class="line">an unexpected $500 expense-national stats office (Feb 2023)</div>
    <div class="line marked">25% of canadians need to access their retirement savings early. 20% of Canadians have no savings.</div>
    <div class="line">39% of canadians aged 55-65 have less Than $5,000 in savings. -federal survey office (June 2023)</div>
  </div>
  <div class="facts facts-debt abs">
    <div class="line marked">The average canadian has $22,131 in consumer debt. Which excludes mortgages.-crediq (Aug 2024)</div>
    <div class="line">Over 55% of canadians hold credit card debt and the total canadian household debt has increased to</div>
    <div class="line marked">$2.52trillion, including consumer credit, mortgage and non-mortgage loans. -national bankers council</div>
    <div class="line">(Aug 2024)</div>
  </div>
  <div class="facts facts-insurance abs">
    <div class="line marked">45% of canadians do not have individual life insurance coverage, but 48% say their families would face</div>
    <div class="line">financial trouble within 6 months of losing someone.-lifeplan research intl. (Apr 2023)</div>
    <div class="line marked">2-in-5 canadians (43% women / 44% men) will be diagosed with a form of cancer or other critical illness</div>
    <div class="line">during their lifetime. Every 7 seconds.-health data office (June 2024)</div>
  </div>

  <svg class="oval abs" width="1082" height="1402" viewBox="0 0 1082 1402" aria-hidden="true">
    <defs><clipPath id="oval-clip"><ellipse cx="541" cy="1071" rx="541" ry="363"/></clipPath></defs>
    <ellipse cx="541" cy="1071" rx="541" ry="363" fill="#0c1b31"/>
    <path d="M225 776 Q541 910 857 776 L900 600 L180 600 Z" fill="#0ea63e" clip-path="url(#oval-clip)"/>
  </svg>

  <h2 class="oval-heading abs">WHO ARE WE AND WHAT<br>DO WE DO?</h2>

  <div class="service abs" style="left:16px;top:871px">
    <div class="badge"><svg viewBox="0 0 64 64" fill="#0ea63e"><rect x="6" y="22" width="52" height="30" rx="3"/><rect x="12" y="14" width="40" height="5" rx="2"/><circle cx="32" cy="37" r="8" fill="#fff"/><circle cx="15" cy="37" r="3" fill="#fff"/><circle cx="49" cy="37" r="3" fill="#fff"/></svg></div>
    <div class="label">CASH FLOW</div>
  </div>
  <div class="service abs" style="left:182px;top:908px">
    <div class="badge"><svg viewBox="0 0 64 64" fill="#0ea63e"><path d="M6 32a26 24 0 0 1 52 0z"/><rect x="30" y="6" width="4" height="6"/><path d="M30 32v18a4 4 0 0 1-8 0" fill="none" stroke="#0ea63e" stroke-width="4"/></svg></div>
    <div class="label">CASH FLOW PROTECTION</div>
  </div>
  <div class="service abs" style="left:368px;top:871px">
    <div class="badge"><svg viewBox="0 0 64 64"><rect x="8" y="14" width="48" height="36" rx="3" fill="none" stroke="#0ea63e" stroke-width="5"/><rect x="8" y="22" width="48" height="6" fill="#0ea63e"/><rect x="14" y="38" width="16" height="4" fill="#0ea63e"/><path d="M8 58L58 6" stroke="#0ea63e" stroke-width="4"/></svg></div>
    <div class="label">DEBT MANAGEMENT</div>
  </div>
  <div class="service abs" style="left:547px;top:908px">
    <div class="badge"><svg viewBox="0 0 64 64" fill="#0ea63e"><path d="M4 18h34v28H4z"/><path d="M38 26h12l10 10v10H38z"/><circle cx="14" cy="48" r="6"/><circle cx="48" cy="48" r="6"/><path d="M18 25h4v5h5v4h-5v5h-4v-5h-5v-4h5z" fill="#fff"/></svg></div>
    <div class="label">EMERGENCY FUND</div>
  </div>
  <div class="service abs" style="left:708px;top:871px">
    <div class="badge"><svg viewBox="0 0 64 64" fill="#0ea63e"><ellipse cx="30" cy="34" rx="22" ry="16"/><rect x="16" y="44" width="7" height="10"/><rect x="36" y="44" width="7" height="10"/><path d="M48 24l8-4v10z"/><rect x="24" y="14" width="12" height="4" rx="2"/></svg></div>
    <div class="label">BUILD WEALTH</div>
  </div>
  <div class="service abs" style="left:865px;top:908px">
    <div class="badge"><svg viewBox="0 0 64 64"><rect x="10" y="8" width="44" height="44" rx="3" fill="none" stroke="#0ea63e" stroke-width="5"/><rect x="18" y="16" width="28" height="28" fill="none" stroke="#0ea63e" stroke-width="3"/><rect x="14" y="52" width="6" height="5" fill="#0ea63e"/><rect x="44" y="52" width="6" height="5" fill="#0ea63e"/><circle cx="32" cy="30" r="3" fill="#0ea63e"/></svg></div>
    <div class="label">PRESERVE</div>
  </div>

  <div class="edu-pill abs">EDUCATION &amp; AWARENESS</div>
  <h2 class="how-heading abs">HOW ARE WE DOING IT?</h2>

  <svg class="abs" style="left:225px;top:1240px" width="120" height="120" viewBox="0 0 120 120" aria-label="Income split into living expenses, taxes and debt" role="img">
    <circle cx="60" cy="60" r="60" fill="#781818"/>
    <path d="M60 0V120M60 60H120" stroke="#fff" stroke-width="2"/>
    <text x="32" y="55" fill="#fff" font-size="9" text-anchor="middle" font-family="Roboto, sans-serif">Living</text>
    <text x="32" y="67" fill="#fff" font-size="9" text-anchor="middle" font-family="Roboto, sans-serif">Expenses</text>
    <text x="87" y="43" fill="#fff" font-size="9" text-anchor="middle" font-family="Roboto, sans-serif">Taxes</text>
    <text x="84" y="90" fill="#fff" font-size="9" text-anchor="middle" font-family="Roboto, sans-serif">Debt</text>
  </svg>

  <svg class="abs" style="left:372px;top:1286px" width="30" height="14" viewBox="0 0 30 14"><path d="M1 7H28M21 1l7 6-7 6" stroke="#fff" stroke-width="1.8" fill="none"/></svg>
  <div class="tiny-label abs" style="left:366px;top:1308px">Savings</div>

  <div class="goal-pill abs" style="top:1239px"><i class="dot"></i><span>Retirement Savings</span></div>
  <div class="goal-pill abs" style="top:1272px"><i class="dot"></i><span>Children Education</span></div>
  <div class="goal-pill abs" style="top:1306px"><i class="dot"></i><span>Proper Protection</span></div>
  <div class="goal-pill abs" style="top:1340px"><i class="dot"></i><span>Freedom From Debt</span></div>

  <svg class="abs" style="left:571px;top:1286px" width="30" height="14" viewBox="0 0 30 14"><path d="M1 7H28M21 1l7 6-7 6" stroke="#fff" stroke-width="1.8" fill="none"/></svg>

  <div class="partner abs" style="left:631px;top:1220px;width:78px"></div>
  <div class="partner abs" style="left:714px;top:1220px;width:82px"></div>
  <div class="partner abs" style="left:631px;top:1252px;width:78px"></div>
  <div class="partner abs" style="left:714px;top:1252px;width:82px"></div>
  <div class="partner abs" style="left:631px;top:1284px;width:78px"></div>
  <div class="partner abs" style="left:714px;top:1284px;width:82px"></div>
  <div class="partner abs" style="left:631px;top:1317px;width:78px"></div>
  <div class="partner abs" style="left:714px;top:1317px;width:82px"></div>
  <div class="partner abs" style="left:631px;top:1349px;width:78px"></div>
  <div class="partner abs" style="left:714px;top:1349px;width:82px"></div>

  <svg class="abs" style="left:827px;top:1286px" width="30" height="14" viewBox="0 0 30 14"><path d="M1 7H28M21 1l7 6-7 6" stroke="#fff" stroke-width="1.8" fill="none"/></svg>
  <div class="tiny-label abs" style="left:822px;top:1308px">Pay Us</div>
</section>

<section class="page page-two">
  <h2 class="rule-heading abs">RULE OF 72</h2>

  <div class="growth-card abs" style="left:79px;top:109px">
    <div class="growth-head"><b>AGE</b><span>4%</span></div>
    <div class="growth-row"><span class="age">29</span><span class="amount">$ 10,000</span></div>
    <div class="growth-row"><span class="age">47</span><span class="amount">$ 20,000</span></div>
    <div class="growth-row"><span class="age">65</span><span class="amount">$ 40,000</span></div>
  </div>
  <div class="growth-note abs" style="left:78px;top:420px">MONEY DOUBLES&nbsp; EVERY 18 YEARS</div>

  <div class="growth-card abs" style="left:400px;top:109px">
    <div class="growth-head"><b>AGE</b><span>6%</span></div>
    <div class="growth-row"><span class="age">29</span><span class="amount">$ 10,000</span></div>
    <div class="growth-row"><span class="age">41</span><span class="amount">$ 20,000</span></div>
    <div class="growth-row"><span class="age">53</span><span class="amount">$ 40,000</span></div>
    <div class="growth-row"><span class="age">65</span><span class="amount">$ 80,000</span></div>
  </div>
  <div class="growth-note abs" style="left:413px;top:495px">MONEY DOUBLES&nbsp; EVERY 12 YEARS</div>

  <div class="growth-card abs" style="left:722px;top:109px">
    <div class="growth-head"><b>AGE</b><span>8%</span></div>
    <div class="growth-row"><span class="age">29</span><span class="amount">$ 10,000</span></div>
    <div class="growth-row"><span class="age">38</span><span class="amount">$ 20,000</span></div>
    <div class="growth-row"><span class="age">47</span><span class="amount">$ 40,000</span></div>
    <div class="growth-row"><span class="age">56</span><span class="amount">$ 80,000</span></div>
    <div class="growth-row"><span class="age">65</span><span class="amount">$ 160,000</span></div>
  </div>
  <div class="growth-note abs" style="left:740px;top:572px">MONEY DOUBLES&nbsp; EVERY 9 YEARS</div>

  <div class="growth-card abs" style="left:79px;top:468px">
    <div class="growth-head"><b>AGE</b><span>12%</span></div>
    <div class="growth-row"><span class="age">29</span><span class="amount">$ 10,000</span></div>
    <div class="growth-row"><span class="age">35</span><span class="amount">$ 20,000</span></div>
    <div class="growth-row"><span class="age">41</span><span class="amount">$ 40,000</span></div>
    <div class="growth-row"><span class="age">47</span><span class="amount">$ 80,000</span></div>
    <div class="growth-row"><span class="age">53</span><span class="amount">$ 160,000</span></div>
    <div class="growth-row"><span class="age">59</span><span class="amount">$ 160,000</span></div>
    <div class="growth-row"><span class="age">65</span><span class="amount">$ 160,000</span></div>
  </div>
  <div class="growth-note abs" style="left:98px;top:1077px">MONEY DOUBLES&nbsp; EVERY 6 YEARS</div>

  <article class="account navy abs" style="top:633px;height:148px">
    <div class="icon"><svg viewBox="0 0 32 32" fill="#fff"><path d="M16 4L2 16h4v12h8v-8h4v8h8V16h4z"/></svg></div>
    <h3>HOME</h3>
    <ul><li>Partner with mortage brokers for best rates.</li><li>Mortage insurance alternatives</li></ul>
    <span class="tag">SELL</span>
  </article>

  <article class="account green abs" style="top:805px;height:150px">
    <div class="icon"><svg viewBox="0 0 32 32" fill="none" stroke="#fff" stroke-width="2.2"><path d="M8 3h12l5 5v21H8z"/><path d="M12 12h8M12 17h9"/><circle cx="10" cy="23" r="6" fill="#0c1b31"/><path d="M7 26l6-6M8 21h.5M12 25h.5"/></svg></div>
    <h3>RRSP</h3>
    <ul><li>Tax Deduction</li><li>Tax Deferred</li></ul>
    <span class="tag">100% TAX</span>
  </article>

  <article class="account navy abs" style="top:978px;height:188px">
    <div class="icon"><svg viewBox="0 0 32 32" fill="#fff"><rect x="5" y="20" width="4" height="8"/><rect x="11" y="16" width="4" height="12"/><rect x="17" y="13" width="4" height="15"/><rect x="23" y="9" width="4" height="19"/><path d="M4 15L14 8l5 3 8-7" fill="none" stroke="#fff" stroke-width="2"/><path d="M23 3h5v5z"/></svg></div>
    <h3>TFSA</h3>
    <ul><li>No Tax Deductions</li><li>Tax Free Growth</li><li>2009 - $95,000</li><li>Limit 2023-$7,000/YR</li></ul>
    <span class="tag">0% TAX</span>
  </article>

  <article class="account green abs" style="top:1190px;height:153px">
    <div class="icon"><svg viewBox="0 0 32 32"><path d="M12 4h8l-3 6h-2z" fill="#fff"/><path d="M13 10h6c6 4 9 10 7 15-1 3-4 4-10 4s-9-1-10-4c-2-5 1-11 7-15z" fill="#fff"/><path d="M13 24l6-7" stroke="#0c1b31" stroke-width="1.8"/><circle cx="13.5" cy="18" r="1.5" fill="#0c1b31"/><circle cx="18.5" cy="23" r="1.5" fill="#0c1b31"/></svg></div>
    <h3>PERM LIFE</h3>
    <ul><li>No Tax Deduction</li><li>Qualify</li><li>Tax Deferred Growth</li></ul>
    <span class="tag">0% TAX</span>
  </article>

  <div class="side-note abs" style="top:1190px">LIFE INSURANCE ILLNESS<br>CRITICAL/DISABILITY</div>
  <div class="side-rule abs"></div>
  <div class="side-note abs" style="top:1278px">DEBT MANAGEMENT<br>CASH FLOW</div>
</section>

</body>
</html>
```